Business Card and Letterhead for Pimlu - modern real estate business

I need a double sided business card design for Pimlu. Please see business card brief here https://files.trelvonadocs.com/sheet/r/7QzTmWbaXLJnoPEd-kRyUgFhHsstbvCe2qfoMxDa_pz/view?mode=shared

Please feel free to design the business cards however you feel best. I am happy to give some creative freedoms and then provide feedback from there.

Please then also create a letterhead to match the business card design

Colors

Designer to choose colors to be used in the design.

Requirements
Must have
• Must be a modern, elegant business card which looks very professional

```html
<!DOCTYPE html>
<html lang="en">
<head>
<meta charset="utf-8">
<title>Pimlu – Business Card</title>
<link rel="stylesheet" href="https://fonts.googleapis.com/css2?family=Raleway:wght@400;500;600;800&display=swap">
<style>
  :root {
    --page: #f2f2f2;
    --card: #0c0c0c;
    --red: #be1e2d;
    --white: #f4f4f4;
    --rule: #d9d9d9;
    --photo-top: #cfd6d6;
    --photo-mid: #8a9a78;
    --photo-low: #2a2a2c;
  }
  * { box-sizing: border-box; margin: 0; padding: 0; }
  html, body {
    width: 1200px; height: 720px; overflow: hidden;
    background: var(--page);
    font-family: "Raleway", sans-serif;
  }
  .sheet {
    width: 1200px; height: 720px;
    display: flex; align-items: center; justify-content: center; gap: 40px;
  }
  .card {
    width: 540px; height: 310px;
    background: var(--card);
    position: relative; overflow: hidden;
    box-shadow: 0 10px 30px rgba(0,0,0,.18);
  }

  /* Front */
  .card-front { padding: 0 48px; display: flex; flex-direction: column; justify-content: center; }
  .front-name {
    color: var(--red); font-weight: 800; font-size: 112px;
    letter-spacing: 6px; line-height: 1; text-align: right;
  }
  .front-rule { height: 2px; background: var(--rule); margin: 14px 0 12px; }
  .tagline {
    color: var(--white); font-weight: 400; font-size: 21px;
    letter-spacing: 4px; white-space: nowrap;
  }
  .tagline .accent { color: var(--red); }

  /* Back */
  .card-back { display: flex; }
  .portrait {
    width: 42%; height: 100%;
    background: linear-gradient(180deg, var(--photo-top) 0%, var(--photo-mid) 45%, var(--photo-low) 100%);
  }
  .details { flex: 1; padding: 18px 20px 0 18px; color: var(--white); }
  .back-name {
    color: var(--red); font-weight: 800; font-size: 46px;
    letter-spacing: 4px; line-height: 1; text-align: right;
  }
  .back-rule { height: 2px; background: var(--rule); margin: 14px 0 0 -18px; }
  .agent-name { font-weight: 600; font-size: 21px; letter-spacing: 3px; margin-top: 28px; }
  .agent-role { font-size: 13px; letter-spacing: 1.6px; margin-top: 4px; }
  .contact { list-style: none; margin-top: 26px; font-size: 13.5px; letter-spacing: 1.8px; line-height: 1.32; }
  .contact .web { color: var(--red); margin-top: 4px; }
</style>
</head>
<body>
<main class="sheet">
  <section class="card card-front" aria-label="Card front">
    <div class="front-name">PIMLU</div>
    <div class="front-rule"></div>
    <p class="tagline">REAL ESTATE DONE <span class="accent">DIFFERENTLY</span></p>
  </section>

  <section class="card card-back" aria-label="Card back">
    <div class="portrait" role="img" aria-label="Portrait photo of the agent in a dark suit against a green valley view"></div>
    <div class="details">
      <div class="back-name">PIMLU</div>
      <div class="back-rule"></div>
      <h1 class="agent-name">DANE HOLLIS</h1>
      <p class="agent-role">Licenced Real Estate Agent</p>
      <ul class="contact">
        <li>0491 570 118</li>
        <li>dane@pimlu.com</li>
        <li>PO Box 1186</li>
        <li>Larkfield NSW 2790</li>
        <li class="web">www.pimlu.com</li>
      </ul>
    </div>
  </section>
</main>
</body>
</html>
```